product development company BRVEMKO LLC business card

We need a business card design for a company based in Texas called 'BRVEMKO LLC'. Our first product is a illuminated portable ice chest that is called ' Copper Harbor coolers'. Copper harbor coolers is trademarked. I would like to have the copper harbor trademark somewhere on the card as well as the BRVEMKO LLC name.

Target Market(s)

outdoor industry

Industry/Entity Type

Business

Contact Information for Business Card

i would like to have BRVEMKO LLC logo larger than the Copper harbor coolers logo.

Font styles to use
Serif
Sans Serif

```html
<!DOCTYPE html>
<html lang="en">
<head>
<meta charset="utf-8">
<title>BRVEMKO LLC Business Card</title>
<link rel="stylesheet" href="https://fonts.googleapis.com/css2?family=Open+Sans:wght@400;600;700&display=swap">
<style>
  :root {
    --backdrop: #6b4a33;
    --card: #020202;
    --ink: #ffffff;
    --ink-soft: #e9e9e9;
  }
  * { margin: 0; padding: 0; box-sizing: border-box; }
  html, body { width: 1200px; height: 1000px; overflow: hidden; }
  body { background: var(--backdrop); position: relative; font-family: "Open Sans", Arial, sans-serif; color: var(--ink); }

  .card {
    position: absolute; left: 265px; width: 666px; height: 397px;
    background: var(--card);
    box-shadow: 0 6px 18px rgba(0,0,0,.45);
  }
  .card--front { top: 73px; }
  .card--back { top: 532px; }

  .company-name {
    position: absolute;
    font-family: "Open Sans", Arial, sans-serif;
    font-weight: 700;
    color: var(--ink);
    line-height: 1;
    white-space: nowrap;
  }
  .card--front .company-name { left: 33px; top: 62px; font-size: 36px; }
  .card--back .company-name { left: 0; width: 100%; top: 172px; font-size: 50px; text-align: center; }

  .contact-person { position: absolute; left: 33px; top: 182px; }
  .contact-person__name { font-weight: 700; font-size: 20px; letter-spacing: .3px; }
  .contact-person__title { font-size: 15px; color: var(--ink-soft); margin-top: 1px; }

  .contact-list { position: absolute; left: 34px; top: 246px; list-style: none; }
  .contact-list__item { display: flex; align-items: center; gap: 8px; font-size: 15px; color: var(--ink-soft); height: 23px; }
  .contact-list__item--address { margin-top: 5px; }
  .contact-list__icon { width: 14px; height: 14px; fill: var(--ink); flex: none; }

  .product-mark { position: absolute; left: 453px; top: 278px; display: flex; align-items: center; gap: 8px; }
  .product-mark__square { width: 38px; height: 38px; background: var(--ink); }
  .product-mark__name { font-weight: 600; font-size: 20px; line-height: 1.05; color: var(--ink); }
</style>
</head>
<body>
  <section class="card card--front">
    <p class="company-name">BRVEMKO LLC</p>

    <div class="contact-person">
      <p class="contact-person__name">MARCUS DEL RIO</p>
      <p class="contact-person__title">Managing Director</p>
    </div>

    <ul class="contact-list">
      <li class="contact-list__item">
        <svg class="contact-list__icon" viewBox="0 0 14 14"><path d="M4 0h6a1 1 0 0 1 1 1v12a1 1 0 0 1-1 1H4a1 1 0 0 1-1-1V1a1 1 0 0 1 1-1zm.5 2v8h5V2zm2.5 9a1 1 0 1 0 0 2 1 1 0 0 0 0-2z"/></svg>
        + 000 000 0000
      </li>
      <li class="contact-list__item">
        <svg class="contact-list__icon" viewBox="0 0 14 14"><path d="M1 4c0-2 2-3 6-3s6 1 6 3v1H10V3.5H4V5H1zm2 2h8l2 6H1zm4 1.5a1.8 1.8 0 1 0 0 3.6 1.8 1.8 0 0 0 0-3.6z"/></svg>
        + 000 000 0000
      </li>
      <li class="contact-list__item">
        <svg class="contact-list__icon" viewBox="0 0 14 14"><path d="M0 3h14v1L7 8 0 4zm0 2.2L7 9.3l7-4.1V11H0z"/></svg>
        info@brvemkocopperharbor.com
      </li>
      <li class="contact-list__item">
        <svg class="contact-list__icon" viewBox="0 0 14 14"><path d="M7 0a7 7 0 1 0 0 14A7 7 0 0 0 7 0zm0 1.5c.8 0 1.7 1.6 2 4H5c.3-2.4 1.2-4 2-4zM5 7h4c-.1 2.9-1.1 5.5-2 5.5S5.1 9.9 5 7zM1.6 6h2c0 .4-.1.7-.1 1 0 1.7.3 3.3.8 4.4A5.5 5.5 0 0 1 1.6 6zm8.8 0h2a5.5 5.5 0 0 1-2.7 5.4c.5-1.1.8-2.7.8-4.4z"/></svg>
        www.brvemkocopperharbor.com
      </li>
      <li class="contact-list__item contact-list__item--address">
        <svg class="contact-list__icon" viewBox="0 0 14 14"><path d="M7 0a5 5 0 0 1 5 5c0 3.5-5 9-5 9S2 8.5 2 5a5 5 0 0 1 5-5zm0 3a2 2 0 1 0 0 4 2 2 0 0 0 0-4z"/></svg>
        4810 W. Mesa Blvd. Alton, TX 78573
      </li>
    </ul>

    <div class="product-mark">
      <span class="product-mark__square"></span>
      <span class="product-mark__name">Copper<br>Harbor</span>
    </div>
  </section>

  <section class="card card--back">
    <p class="company-name">BRVEMKO LLC</p>
  </section>
</body>
</html>
```